Etiketten-Design für nachhaltige Rasur- & Pflegeprodukte
> Wir suchen Verpackung und Etiketten für eine Marke für nachhaltige Rasur- & Pflegeprodukte.
Habedere liebe Designer,
„Habedere“ sagt man bei uns in Bayern, es bedeutet Hallo oder auf Wiedersehen, je nach Gelegenheit. In diesem Fall: Hallo.
Vielleicht kennst du uns schon, wir sind greenpines, wir betreiben einen kleinen Shop für Bartpflege & Rasur unter greenpines-shop.de und wir versuchen uns nun an einem neuen Thema: nachhaltige Rasur- & Pflegeprodukte für Frauen.
Das machen wir unter dem Namen „Sanft“.
Weil die Frage schon oft aufkam: Jawohl, wir haben uns dafür die Beine und die Achseln mit einem Rasierhobel rasiert.
> Zielgruppe.
Wir arbeiten an einer neuen Pflegelinie für Frauen, die sich vorwiegend mit der Rasur und den dazugehörigen Pflegeprodukten beschäftigt. Die Zielgruppe sind vor allem online-affine Frauen aus Deutschland, Österreich und der Schweiz, aber sicher auch europaweit im Alter von 21-45.
> Aufgabenstellung.
Wir sind auf der Suche nach einem Konzept für unsere Produktverpackungen bzw. Etiketten. Bei den Pflegeprodukten verzichten wir bewusst auf eine Umverpackung.
Konkret geplant sind ein Rasierhobel, dafür haben wir eine schöne Umverpackung. Außerdem starten wir mit Rasieröl, Rasierseife und einem After Shave Balsam. Es werden später noch andere Artikel dazukommen, eine Deocreme zum Beispiel.
Rasieröl, Rasiercreme und After Shave Balsam duften nach Orangen, es werden zwei oder drei weitere Duftrichtungen folgen, die eine wird beispielsweise nach Beeren duften, die andere nach Pfirsich und Mango – bitte beachte das bei der Erstellung des Konzeptes, die Unterschiede sollten später auf den ersten Blick erkennbar sein.
Zurück zum Thema Orange: Wir würden den Duft als leicht herben Zitrusduft bezeichnen.
> Die Maße.
• Umverpackung Rasierhobel, weißer Karton (165x90x40mm)
• Rasieröl 30ml (Etikett: 100x46mm)
• Rasiercreme 60ml (Etikett: 156x32mm)
• After Shave Balsam 60ml (Etikett: 156x32mm)
> Zwingend erforderliche Angaben.
Da es sich um Kosmetikprodukte handelt, sind einige Angaben auf dem Label zwingend erforderlich, beispielhaft sollen die folgenden Infos als Platzhalter dienen.
• Hergestellt für Friedrich Lautner e.K. von greenpines, Lindenhofweg 7, 83109 Kolbermoor
• Ingredients: Aqua, Stearic Acid, Cocos Nucifera oil, Glycerin, Potassium Hydroxide, Litsea Cubeba oil, (and) Citrus Sinensis Peel oil, Orbignya Oleifera oil, Sodium Hydroxide, Macadamia ternifolia oil, Talc, Kaolin, Citric Acid, Simmondsia chinensis oil, Maris sal, C.I. 77892 (and) Rad Clay, Citral, Limonene, Linalool, Geraniol
• Platz für einen Barcode
• Rasieröl sind 30ml / 1.01 FL.OZ. ODER Creme & Balsam jeweils 60ml / 2.03 FL. OZ.
Wir haben ein Bild der aktuellen Gefäße beigefügt, es kann aber durchaus sein, dass wir uns noch umen..

```html
<!DOCTYPE html>
<html lang="de">
<head>
<meta charset="utf-8">
<title>Sanft Rasieröl – Etikettenentwürfe</title>
<link rel="stylesheet" href="https://fonts.googleapis.com/css2?family=Cormorant+Garamond:wght@500;600&family=Tinos:wght@700&family=Oswald:wght@500&family=Jost:wght@400;500&family=Caveat:wght@500&display=swap">
<style>
  :root {
    --page-bg: #eceee4;
    --label-bg: #ffffff;
    --rust: #c4500f;
    --orange: #e0670f;
    --teal-dark: #4b7069;
    --teal-title: #3f6b61;
    --teal-soft: #8fb3ac;
    --teal-volume: #7fa39c;
    --ink: #1d1d1d;
    --barcode-space: #8c8c8c;
    --art-orange-a: #f3c79b;
    --art-orange-b: #e9a265;
    --art-sage-a: #dfe3da;
    --art-sage-b: #b6bfb1;
  }
  * { margin: 0; padding: 0; box-sizing: border-box; }
  html, body { width: 1200px; height: 612px; overflow: hidden; }
  body { background: var(--page-bg); position: relative; }

  .label {
    position: absolute;
    width: 549px; height: 251px;
    background: var(--label-bg);
    overflow: hidden;
    box-shadow: 0 2px 8px rgba(0,0,0,.12);
  }
  .label--tl { left: 39px;  top: 43px; }
  .label--tr { left: 624px; top: 43px; }
  .label--bl { left: 39px;  top: 329px; }
  .label--br { left: 624px; top: 329px; }

  .band { position: absolute; left: 0; width: 100%; }
  .band--top { top: 0; height: 8px; }
  .band--bottom { bottom: 0; height: 9px; }
  .theme-rust .band { background: var(--rust); }
  .theme-orange .band { background: var(--orange); }
  .theme-teal .band { background: var(--teal-dark); }

  .brand {
    position: absolute;
    width: 54px; height: 54px; border-radius: 50%;
    display: flex; align-items: center; justify-content: center;
    color: #fff;
    font-family: "Cormorant Garamond", serif; font-weight: 600; font-size: 17px;
  }
  .brand--rust { background: var(--rust); }
  .brand--teal { background: var(--teal-soft); }

  .title {
    position: absolute;
    font-family: "Cormorant Garamond", serif; font-weight: 500;
    font-size: 45px; line-height: 1; white-space: nowrap;
  }
  .title--rust { color: var(--rust); left: 42px; top: 86px; }
  .title--center { color: var(--teal-title); left: 0; width: 549px; text-align: center; top: 75px; font-size: 42px; }
  .title--script {
    font-family: "Caveat", cursive; font-weight: 500; font-size: 44px;
    color: var(--teal-soft); left: 58px; top: 86px; letter-spacing: 1px;
  }

  .volume {
    position: absolute;
    font-family: "Oswald", sans-serif; font-weight: 500; font-size: 22px; line-height: 1;
  }
  .volume--rust { color: var(--rust); left: 226px; top: 213px; }
  .volume--teal { color: var(--teal-volume); left: 226px; top: 215px; }
  .volume--center { color: var(--teal-volume); left: 0; width: 549px; text-align: center; top: 211px; }

  .art { position: absolute; border-radius: 40px 40px 20px 20px; }
  .art--orange { background: radial-gradient(ellipse at 50% 55%, var(--art-orange-b), var(--art-orange-a) 65%, rgba(255,255,255,0) 100%); }
  .art--sage { background: radial-gradient(ellipse at 50% 55%, var(--art-sage-b), var(--art-sage-a) 65%, rgba(255,255,255,0) 100%); }
  .art--side { left: 3px; top: 143px; width: 167px; height: 93px; }
  .art--center { left: 165px; top: 116px; width: 204px; height: 86px; }
  .art--slice { left: 176px; top: 21px; width: 79px; height: 59px; border-radius: 50%; }

  .legal {
    position: absolute; left: 350px; top: 51px; width: 156px;
    color: var(--ink); text-transform: uppercase; text-align: justify;
    font-size: 5.8px; line-height: 7px;
  }
  .legal p + p { margin-top: 7px; }
  .legal--serif { font-family: "Tinos", serif; font-weight: 700; }
  .legal--sans { font-family: "Jost", sans-serif; font-weight: 400; left: 354px; top: 56px; width: 155px; }

  .barcode-space { position: absolute; background: var(--barcode-space); }
  .barcode-space--wide { left: 382px; top: 162px; width: 99px; height: 39px; }
  .barcode-space--tall { left: 39px; top: 76px; width: 39px; height: 99px; }

  .vertical {
    position: absolute;
    transform: rotate(-90deg); transform-origin: 0 0;
    font-family: "Jost", sans-serif; font-weight: 500;
    color: var(--ink); text-transform: uppercase; text-align: justify;
  }
  .vertical--maker { left: 13px; top: 200px; width: 156px; font-size: 3.6px; line-height: 4.4px; }
  .vertical--ingredients { left: 506px; top: 225px; width: 206px; font-size: 3.2px; line-height: 3.5px; }
  .vertical--about { left: 466px; top: 224px; width: 203px; font-size: 3.2px; line-height: 3.6px; }
</style>
</head>
<body>

<!-- Variante 1: Rost, Serif -->
<section class="label label--tl theme-rust">
  <div class="band band--top"></div>
  <div class="brand brand--rust" style="left:101px;top:16px;">Sanft</div>
  <h1 class="title title--rust">RASIERÖL</h1>
  <div class="art art--orange art--side" role="img" aria-label="Zeichnung von Orangen, Orangenscheiben und Blüten in Orange"></div>
  <div class="volume volume--rust">30ML</div>
  <div class="legal legal--serif">
    <p>Ingredients: Aqua, Stearic Acid, Cocos Nucifera oil, Glycerin, Potassium Hydroxide, Litsea Cubeba oil, (and) Citrus Sinensis Peel oil, Orbignya Oleifera oil, Sodium Hydroxide, Macadamia ternifolia oil, Talc, Kaolin, Citric Acid, Simmondsia chinensis oil, Maris sal, C.I. 77892 (and) Rad Clay, Citral, Limonene, Linalool, Geraniol</p>
    <p>Hergestellt für Friedrich Lautner e.K. von greenpines, Lindenhofweg 7, 83109 Kolbermoor</p>
  </div>
  <div class="barcode-space barcode-space--wide"></div>
  <div class="band band--bottom"></div>
</section>

<!-- Variante 2: Orange, zentriert -->
<section class="label label--tr theme-orange">
  <div class="band band--top"></div>
  <div class="vertical vertical--maker">Hergestellt für Friedrich Lautner e.K. von greenpines, Lindenhofweg 7, 83109 Kolbermoor</div>
  <div class="barcode-space barcode-space--tall"></div>
  <div class="brand brand--teal" style="left:245px;top:17px;width:50px;height:50px;font-size:16px;">Sanft</div>
  <h1 class="title title--center">RASIERÖL</h1>
  <div class="art art--orange art--center" role="img" aria-label="Zeichnung von Orangen, Orangenscheiben und Blüten in Orange"></div>
  <div class="volume volume--center">30ML</div>
  <div class="vertical vertical--ingredients">Ingredients: Aqua, Stearic Acid, Cocos Nucifera oil, Glycerin, Potassium Hydroxide, Litsea Cubeba oil, (and) Citrus Sinensis Peel oil, Orbignya Oleifera oil, Sodium Hydroxide, Macadamia ternifolia oil, Talc, Kaolin, Citric Acid, Simmondsia chinensis oil, Maris sal, C.I. 77892 (and) Rad Clay, Citral, Limonene, Linalool, Geraniol</div>
  <div class="band band--bottom"></div>
</section>

<!-- Variante 3: Salbei, Schreibschrift -->
<section class="label label--bl theme-teal">
  <div class="band band--top"></div>
  <div class="brand brand--teal" style="left:101px;top:16px;">Sanft</div>
  <div class="art art--sage art--slice" role="img" aria-label="Zeichnung einer Orangenscheibe und eines Orangenschnitzes in Grau"></div>
  <h1 class="title title--script">RASIERÖL</h1>
  <div class="art art--sage art--side" role="img" aria-label="Zeichnung von Orangen, Orangenscheiben und Blüten in Salbeigrau"></div>
  <div class="volume volume--teal">30ML</div>
  <div class="legal legal--sans">
    <p>Ingredients: Aqua, Stearic Acid, Cocos Nucifera oil, Glycerin, Potassium Hydroxide, Litsea Cubeba oil, (and) Citrus Sinensis Peel oil, Orbignya Oleifera oil, Sodium Hydroxide, Macadamia ternifolia oil, Talc, Kaolin, Citric Acid, Simmondsia chinensis oil, Maris sal, C.I. 77892 (and) Rad Clay, Citral, Limonene, Linalool, Geraniol</p>
    <p>Hergestellt für Friedrich Lautner e.K. von greenpines, Lindenhofweg 7, 83109 Kolbermoor</p>
  </div>
  <div class="barcode-space barcode-space--wide"></div>
  <div class="band band--bottom"></div>
</section>

<!-- Variante 4: Salbei, zentriert mit Beschreibung -->
<section class="label label--br theme-teal">
  <div class="band band--top"></div>
  <div class="vertical vertical--maker">Hergestellt für Friedrich Lautner e.K. von greenpines, Lindenhofweg 7, 83109 Kolbermoor</div>
  <div class="barcode-space barcode-space--tall"></div>
  <div class="brand brand--teal" style="left:245px;top:17px;width:50px;height:50px;font-size:16px;">Sanft</div>
  <h1 class="title title--center">RASIERÖL</h1>
  <div class="art art--sage art--center" role="img" aria-label="Zeichnung von Orangen, Orangenscheiben und Blüten in Salbeigrau"></div>
  <div class="volume volume--center">30ML</div>
  <div class="vertical vertical--about">Um deiner Rasurvorbereitung eine neue Komponente zu verpassen eignet sich Rasieröl hervorragend. Es kann Rasurbrand, Rötungen und Hautreizungen vorbeugen, pflegt somit also deine Haut und spendet ihr zusätzlich Feuchtigkeit.</div>
  <div class="vertical vertical--ingredients">Ingredients: Aqua, Stearic Acid, Cocos Nucifera oil, Glycerin, Potassium Hydroxide, Litsea Cubeba oil, (and) Citrus Sinensis Peel oil, Orbignya Oleifera oil, Sodium Hydroxide, Macadamia ternifolia oil, Talc, Kaolin, Citric Acid, Simmondsia chinensis oil, Maris sal, C.I. 77892 (and) Rad Clay, Citral, Limonene, Linalool, Geraniol</div>
  <div class="band band--bottom"></div>
</section>

</body>
</html>
```